Brell Stone Company Business Cards

Front and Back Business Card - logo and text setup - cool design. I need workable photoshop or illustrator files so I can setup each employee card with design that is created
Updates

Hi everyone, thank you for the great entries. Please no more white and blue cards - there are so many already - black and silver only now please. thanks!

Target Market(s)

Construction Industry - Facility Managers

Industry/Entity Type

Construction

Contact Information for Business Card

I really like contemporary simplistic looks - clean neat....not opposed to seeing some black backrounds

Requirements
Must have
• Logo/website address with design on front only - www.brellstone-example.com (logo attached)
• Back:
• Name/Title/Company Address/Phone/email address
Nice to have
• Cool design
Should not have
• Nothing gimmicky like Fire or Water - since we are a Fire Protection company - it has all been done

```html
<!DOCTYPE html>
<html lang="en">
<head>
<meta charset="utf-8">
<title>Brell Stone Company Business Cards</title>
<link href="https://fonts.googleapis.com/css2?family=Lato:wght@400;700&display=swap" rel="stylesheet">
<style>
  :root {
    --backdrop: #8f8f8f;
    --black: #151617;
    --silver: #d4d7db;
    --silver-light: #e9ebee;
    --silver-mid: #a9aeb4;
    --steel: #5f656c;
    --ink: #2b2e32;
    --rule: #b3b8be;
  }
  * { margin: 0; padding: 0; box-sizing: border-box; }
  html, body { width: 1200px; height: 900px; overflow: hidden; }
  body {
    background: var(--backdrop);
    font-family: "Lato", sans-serif;
    position: relative;
  }
  .card {
    position: absolute;
    top: 275px;
    width: 477px;
    height: 294px;
    box-shadow: 2px 3px 4px rgba(0,0,0,0.45);
  }
  .card-details {
    left: 120px;
    background: linear-gradient(135deg, var(--silver-light), var(--silver));
    border-radius: 0 62px 0 62px;
  }
  .card-brand {
    left: 620px;
    background: var(--black);
    border-radius: 62px 0 62px 0;
  }
  .wordmark {
    position: absolute;
    font-weight: 700;
    white-space: nowrap;
    display: flex;
    align-items: center;
    gap: 8px;
  }
  .wordmark-mark {
    display: inline-block;
    width: 10px;
    height: 10px;
  }
  .card-details .wordmark {
    left: 52px;
    top: 124px;
    font-size: 31px;
    color: var(--black);
  }
  .card-details .wordmark-mark { background: var(--steel); }
  .card-brand .wordmark {
    left: 0;
    right: 0;
    top: 112px;
    justify-content: center;
    font-size: 46px;
    color: var(--silver);
  }
  .card-brand .wordmark-mark { width: 14px; height: 14px; background: var(--silver-mid); }
  .website {
    position: absolute;
    left: 0;
    right: 0;
    top: 180px;
    text-align: center;
    font-size: 14px;
    letter-spacing: 1px;
    color: var(--silver-mid);
  }
  .divider {
    position: absolute;
    left: 251px;
    top: 70px;
    width: 1px;
    height: 150px;
    background: var(--rule);
  }
  .contact {
    position: absolute;
    left: 268px;
    top: 87px;
    color: var(--ink);
    font-size: 14px;
    line-height: 18px;
  }
  .contact-name {
    font-size: 17px;
    line-height: 20px;
    color: var(--black);
    text-transform: uppercase;
  }
  .contact-name .surname { color: var(--steel); }
  .contact-title { margin-bottom: 4px; }
  .contact-line { display: flex; align-items: center; gap: 5px; }
  .contact-line svg { width: 11px; height: 11px; fill: var(--black); flex: none; }
  .contact-email { font-size: 13px; }
  .contact-address { margin-top: 5px; padding-left: 1px; }
</style>
</head>
<body>
  <section class="card card-details">
    <div class="wordmark"><span class="wordmark-mark"></span>Brell Stone</div>
    <div class="divider"></div>
    <div class="contact">
      <div class="contact-name">Daniel <span class="surname">Marsh</span></div>
      <div class="contact-title">Managing Director</div>
      <div class="contact-line">
        <svg viewBox="0 0 12 12" aria-hidden="true"><path d="M1 4.5C1 2.5 3.5 1.5 6 1.5s5 1 5 3v1H8.5V4.3C7.8 4 6.9 3.9 6 3.9S4.2 4 3.5 4.3v1.2H1z M2.5 6.5h7L10.5 10.5h-9z"/></svg>
        <span>044-555 010 234</span>
      </div>
      <div class="contact-line">
        <svg viewBox="0 0 12 12" aria-hidden="true"><path d="M1 2.5h10v7H1z M1.6 3.2 6 6.6l4.4-3.4" stroke="#e9ebee" stroke-width="0.9"/></svg>
        <span class="contact-email">info@brellstone-example.com</span>
      </div>
      <div class="contact-address">421, Address line here,<br>45452,Country Name</div>
    </div>
  </section>

  <section class="card card-brand">
    <div class="wordmark"><span class="wordmark-mark"></span>Brell Stone</div>
    <div class="website">www.brellstone-example.com</div>
  </section>
</body>
</html>
```